Health Coaching website focused on diabetes management using Vantelo template

I am starting a health coaching business and would like to use Plumestack and an Vantelo template. The coaching will focus on Pre-diabetic and chronic disease patients so it will need to have a personal as well as a slight clinical look to it. The site should have an overall look similar to Meadow Loop theme. I will purchase the Vantelo designer package for use.

Target Market(s)

40-60 year olds with pre-diabetes or concerned about chronic disease, maintaining health, nutrition and weight loss

Industry/Entity Type

Health And Wellness

Number of Pages Required

5+ page

Colors
87cfc6
60b9df
fee18a
00a990
3276b5

Requirements
Must have
• It should contain an ecommerce tab, member's only area, interactive blog, built-in SEO and an opt-in area on every page. It should have several call to actions throughout the site. The site should have an overall look similar to Meadow Loop theme. Hosting on Servunda. Also needed all the essential plumestack plugins:
• Keystep forms & Keystep entry pages
• Pondra Metrics
• Vantelo shield plus
• Postwren
• Valdeno
• Vault Parrot
• Kindle SEO
• Drifting Share Strip
• Q7 Rapid Store
• Tembi
Nice to have
• Ecommerce ready with cartoflex plugin
• Hi-res pictures of people in my demographic enjoying life and/or exercising, cooking, etc.
Should not have
• slider on homepage
• my profile on homepage

```html
<!DOCTYPE html>
<html lang="en">
<head>
<meta charset="utf-8">
<title>Evenkeel Wellness – Our Courses</title>
<link rel="stylesheet" href="https://fonts.googleapis.com/css2?family=Open+Sans:wght@300;400;600;700&display=swap">
<style>
:root{
  --green:#00a990;
  --green-soft:#87cfc6;
  --blue:#3276b5;
  --sky:#60b9df;
  --sun:#fee18a;
  --band:#e3f1f8;
  --ink:#444a4f;
  --muted:#7a8288;
  --footer:#2d3236;
  --footer-deep:#22262a;
  --white:#ffffff;
}
*{box-sizing:border-box;margin:0;padding:0}
html,body{width:1200px;height:2796px;overflow:hidden}
body{font-family:"Open Sans",Arial,sans-serif;color:var(--ink);background:var(--white);font-size:14px;line-height:1.6}
.wrap{width:860px;margin:0 auto}
.wide{width:1040px;margin:0 auto}

/* header */
.site-header{height:120px}
.site-header .wide{display:flex;align-items:center;justify-content:space-between;height:120px}
.brand{display:flex;align-items:center;gap:14px}
.brand-dot{width:46px;height:46px;border-radius:50%;background:var(--green)}
.brand-name{font-size:30px;font-weight:600;color:var(--green);line-height:1}
.header-actions{display:flex;align-items:center;gap:26px}
.phone{display:flex;align-items:center;gap:10px;font-size:20px;font-weight:600;color:var(--ink)}
.phone svg{width:34px;height:34px}
.btn{display:inline-block;background:var(--green);color:var(--white);font-size:13px;font-weight:600;letter-spacing:.5px;text-transform:uppercase;padding:12px 22px;border-radius:3px}
.main-nav{height:28px;background:var(--blue)}
.main-nav ul{list-style:none;display:flex;justify-content:center;height:28px}
.main-nav li{color:var(--white);font-size:12px;font-weight:600;padding:0 24px;line-height:28px;text-transform:uppercase}
.main-nav li.active{background:var(--green)}

/* hero */
.hero{height:324px;position:relative;background:linear-gradient(90deg,#b59070 0%,#d9c3a3 35%,#efe7d8 60%,#f4efe7 100%)}
.hero-text{position:absolute;right:200px;top:70px;text-align:center;color:var(--white)}
.hero-text h2{font-size:50px;font-weight:400;line-height:1.1;text-shadow:0 1px 3px rgba(0,0,0,.25)}
.hero-text p{font-size:20px;margin-top:8px;text-shadow:0 1px 3px rgba(0,0,0,.25)}
.dots{display:flex;gap:8px;justify-content:center;margin-top:18px}
.dots span{width:12px;height:12px;border-radius:50%;background:rgba(255,255,255,.6)}
.dots span.on{background:var(--green)}

.crumbs{height:32px;background:#f1f3f4;font-size:12px;color:var(--muted);line-height:32px}
.crumbs .wide{padding-left:6px}

/* page title */
.page-title{text-align:center;padding-top:40px;height:110px}
.page-title h1{font-size:34px;font-weight:400;color:var(--ink)}
.page-title h1 span{color:var(--green)}
.page-title .rule{width:70px;height:3px;background:var(--green);margin:8px auto 0}

.section-title{text-align:center;color:var(--green);font-size:28px;font-weight:700;line-height:1.4}

/* course one */
.course-intro{height:390px;padding-top:10px}
.split{display:flex;gap:36px;margin-top:28px}
.split .copy{flex:1;font-size:13px}
.copy p{margin-bottom:12px}
.copy strong{color:var(--ink)}
.photo{flex:0 0 340px;height:220px;border-radius:2px}
.photo-meter{background:linear-gradient(135deg,#7d8690,#c8ccd0 55%,#eef0f1)}
.quote{text-align:center;color:var(--sky);font-size:19px;font-weight:600;margin-top:20px}

.coach-band{height:400px;background:var(--band);position:relative}
.coach-band .wrap{display:flex;height:400px}
.photo-couple{flex:0 0 420px;height:400px;background:linear-gradient(90deg,#9bc58a 0%,#c9d8b4 40%,#e4ebe0 100%)}
.coach-copy{padding:34px 0 0 36px;flex:1}
.coach-copy h3{color:var(--blue);font-size:16px;font-weight:600;line-height:1.45}
.ticks{list-style:none;margin:18px 0 20px}
.ticks li{display:flex;align-items:center;gap:10px;font-size:13px;font-weight:600;margin-bottom:7px}
.ticks svg{width:14px;height:14px;flex:none}

/* course two */
.nutrition{height:476px;padding-top:52px}
.nutrition .split{margin-top:30px;align-items:flex-start}
.photo-scale{flex:0 0 360px;height:250px;background:linear-gradient(135deg,#f4f4f2,#d8e3c8 45%,#c8543f 75%,#e9d7a6)}
.nutrition .copy{font-size:12.5px;line-height:1.55}
.nutrition .copy p{margin-bottom:8px}
.nutrition .copy h4{color:var(--blue);font-size:14px;font-weight:700;margin-bottom:2px}
.nutrition .closing{font-size:12.5px;line-height:1.55;margin-top:14px}

.benefit-band{height:440px;background:var(--band)}
.benefit-band .wrap{display:flex;height:440px}
.benefit-copy{flex:1;padding-top:70px}
.benefit-copy h4{color:var(--green);font-size:17px;font-weight:700}
.benefit-copy .note{font-size:12.5px;margin-top:6px;width:400px}
.photo-cook{flex:0 0 420px;height:440px;background:linear-gradient(90deg,#e7eef1,#d7e6ea 40%,#9fc6d6 70%,#f1d8c4)}

.cta-row{height:72px;padding-top:16px}

/* footer */
.site-footer{height:368px;background:var(--footer);color:#c8ced2}
.site-footer .wide{display:flex;padding-top:42px;gap:60px}
.foot-col h5{font-size:15px;font-weight:700;color:var(--white);text-transform:uppercase;margin-bottom:16px}
.foot-col h5 span{color:var(--green);font-weight:400}
.foot-col ul{list-style:none;font-size:13px;line-height:1.9}
.quick{flex:0 0 170px}
.quick li::before{content:"› ";color:var(--green)}
.contact{flex:0 0 260px;font-size:13px}
.contact .line{display:flex;gap:8px;align-items:center;margin-bottom:6px}
.contact svg{width:14px;height:14px;flex:none}
.follow{flex:0 0 200px}
.follow li{display:flex;align-items:center;gap:12px;margin-bottom:10px}
.follow li i{width:24px;height:24px;border-radius:50%;background:var(--blue);display:block}
.foot-mark{flex:1;display:flex;align-items:center;justify-content:center;font-size:26px;font-weight:600;color:#4a5258}
.copyright{height:36px;background:var(--footer-deep);color:#8c949a;font-size:12px;line-height:36px}
</style>
</head>
<body>

<header class="site-header">
  <div class="wide">
    <div class="brand"><span class="brand-dot"></span><span class="brand-name">Evenkeel Wellness</span></div>
    <div class="header-actions">
      <div class="phone">
        <svg viewBox="0 0 34 34"><circle cx="17" cy="17" r="17" fill="#00a990"/><path d="M12 9c1 0 2 2.5 2.5 3.5.3.8-1 1.6-1.3 2.2.8 2 2.5 3.6 4.4 4.5.6-.4 1.4-1.6 2.2-1.3 1 .5 3.5 1.5 3.5 2.5 0 1.2-1.6 3-3 3C14.5 23.4 10.6 19.5 10 13c0-1.4 1-4 2-4z" fill="#fff"/></svg>
        630-555-0184
      </div>
      <span class="btn">Book an appointment</span>
    </div>
  </div>
</header>
<nav class="main-nav">
  <ul>
    <li>Home</li><li>About Evenkeel</li><li class="active">Our Courses</li><li>Special Offers</li><li>Testimonials</li><li>Blog</li><li>FAQs</li><li>Contact Us</li>
  </ul>
</nav>

<section class="hero" role="img" aria-label="Photo of a mature couple cooking fresh vegetables together in a bright kitchen">
  <div class="hero-text">
    <h2>Evenkeel<br>For Wellness</h2>
    <p>Get the health and lifestyle<br>you want now!</p>
    <div class="dots"><span class="on"></span><span></span><span></span><span></span></div>
  </div>
</section>

<div class="crumbs"><div class="wide">Home &gt; Our Courses</div></div>

<div class="page-title">
  <h1>Our <span>Courses</span></h1>
  <div class="rule"></div>
</div>

<section class="course-intro">
  <div class="wrap">
    <h2 class="section-title">Pre-Diabetes and Chronic Disease</h2>
    <div class="split">
      <div class="copy">
        <p><strong>Is your health out of control? Get it back!</strong><br>If you have received a diagnosis of pre-diabetes or diabetes type II, don't let it overwhelm you. It's tough and can be difficult to comprehend at first, but it is completely manageable and even reversible. Yes, diabetes type II can be reversed with lasting lifestyle changes you can keep.</p>
        <p>Understanding the underlying causes and conditions of diabetes and chronic disease is the first step to managing and reversing the damage. Education is an important part of this process and I approach the disease from a whole person perspective, combining proven programs with personal coaching so you develop a sustained approach to being improved health and well being from an integrated body system perspective.</p>
      </div>
      <div class="photo photo-meter" role="img" aria-label="Photo of a blood glucose meter and test strip in a hand"></div>
    </div>
    <p class="quote">Think of what it would feel like to lose weight, gain energy and feel great again!</p>
  </div>
</section>

<section class="coach-band">
  <div class="wrap">
    <div class="photo-couple" role="img" aria-label="Photo of a smiling older couple standing together outdoors"></div>
    <div class="coach-copy">
      <h3>As a National Diabetes Lifestyle Coach and Chronic Care Educator, I use the most recent, scientifically proven methods developed to:</h3>
      <ul class="ticks">
        <li><svg viewBox="0 0 14 14"><circle cx="7" cy="7" r="7" fill="#00a990"/><path d="M4 7.2l2 2 4-4.4" stroke="#fff" stroke-width="1.6" fill="none"/></svg>Need less medications</li>
        <li><svg viewBox="0 0 14 14"><circle cx="7" cy="7" r="7" fill="#00a990"/><path d="M4 7.2l2 2 4-4.4" stroke="#fff" stroke-width="1.6" fill="none"/></svg>Get more energy</li>
        <li><svg viewBox="0 0 14 14"><circle cx="7" cy="7" r="7" fill="#00a990"/><path d="M4 7.2l2 2 4-4.4" stroke="#fff" stroke-width="1.6" fill="none"/></svg>Stop blood sugar swings</li>
        <li><svg viewBox="0 0 14 14"><circle cx="7" cy="7" r="7" fill="#00a990"/><path d="M4 7.2l2 2 4-4.4" stroke="#fff" stroke-width="1.6" fill="none"/></svg>Lose weight</li>
        <li><svg viewBox="0 0 14 14"><circle cx="7" cy="7" r="7" fill="#00a990"/><path d="M4 7.2l2 2 4-4.4" stroke="#fff" stroke-width="1.6" fill="none"/></svg>Build more muscle</li>
        <li><svg viewBox="0 0 14 14"><circle cx="7" cy="7" r="7" fill="#00a990"/><path d="M4 7.2l2 2 4-4.4" stroke="#fff" stroke-width="1.6" fill="none"/></svg>Decrease stress</li>
        <li><svg viewBox="0 0 14 14"><circle cx="7" cy="7" r="7" fill="#00a990"/><path d="M4 7.2l2 2 4-4.4" stroke="#fff" stroke-width="1.6" fill="none"/></svg>Stop feeling bloated and miserable</li>
        <li><svg viewBox="0 0 14 14"><circle cx="7" cy="7" r="7" fill="#00a990"/><path d="M4 7.2l2 2 4-4.4" stroke="#fff" stroke-width="1.6" fill="none"/></svg>Stop wasting money on medications</li>
      </ul>
      <span class="btn">Free consultation</span>
    </div>
  </div>
</section>

<section class="nutrition">
  <div class="wrap">
    <h2 class="section-title">Nutrition and Weight Management</h2>
    <div class="split">
      <div class="photo photo-scale" role="img" aria-label="Photo of a bathroom scale surrounded by fresh fruit and a measuring tape"></div>
      <div class="copy">
        <p>Our culture pushes us towards unhealthy eating everywhere we look. Calories are cheap, fast foods everywhere are on every corner. Convenience stores have gimmicks, prepackaged food with little nutritional value. We've got bad work habits of over scheduling and over committing. This stress can mess up our sleep and makes us unhealthy food choices that harm our bodies.</p>
        <h4>It's time to stop the insanity!</h4>
        <p>It's time to make health priority #1! My partner with you to reduce stress, create a real and friendly plan that works with your life, simplify meals and smart choices. Start easy, build the way you want to. When you commit to a lifestyle that works with your schedule, it becomes part of your daily life, not daily struggle.</p>
      </div>
    </div>
    <p class="closing">Our healthstyle programs are individually structured to uncover what could block your path to a healthy lifestyle in the past and develop new approaches to creating healthy habits for the future. Our scientifically proven approaches will motivate and inspire you to create the life you've always imagined.</p>
  </div>
</section>

<section class="benefit-band">
  <div class="wrap">
    <div class="benefit-copy">
      <h4>You will:</h4>
      <ul class="ticks">
        <li><svg viewBox="0 0 14 14"><circle cx="7" cy="7" r="7" fill="#00a990"/><path d="M4 7.2l2 2 4-4.4" stroke="#fff" stroke-width="1.6" fill="none"/></svg>Lose weight</li>
        <li><svg viewBox="0 0 14 14"><circle cx="7" cy="7" r="7" fill="#00a990"/><path d="M4 7.2l2 2 4-4.4" stroke="#fff" stroke-width="1.6" fill="none"/></svg>Decrease cravings and stabilize your blood sugar</li>
        <li><svg viewBox="0 0 14 14"><circle cx="7" cy="7" r="7" fill="#00a990"/><path d="M4 7.2l2 2 4-4.4" stroke="#fff" stroke-width="1.6" fill="none"/></svg>Increase your energy</li>
        <li><svg viewBox="0 0 14 14"><circle cx="7" cy="7" r="7" fill="#00a990"/><path d="M4 7.2l2 2 4-4.4" stroke="#fff" stroke-width="1.6" fill="none"/></svg>Build more muscle</li>
        <li><svg viewBox="0 0 14 14"><circle cx="7" cy="7" r="7" fill="#00a990"/><path d="M4 7.2l2 2 4-4.4" stroke="#fff" stroke-width="1.6" fill="none"/></svg>Decrease stress</li>
        <li><svg viewBox="0 0 14 14"><circle cx="7" cy="7" r="7" fill="#00a990"/><path d="M4 7.2l2 2 4-4.4" stroke="#fff" stroke-width="1.6" fill="none"/></svg>Stop feeling bloated and miserable</li>
      </ul>
      <p class="note">Don't delay, you're now Evenkeel a waiting for your calls on the 30 mins consultation.</p>
    </div>
    <div class="photo-cook" role="img" aria-label="Photo of a smiling woman preparing a fresh salad in a kitchen"></div>
  </div>
</section>

<div class="cta-row"><div class="wrap"><span class="btn">Free consultation</span></div></div>

<footer class="site-footer">
  <div class="wide">
    <div class="foot-col quick">
      <h5>Quick <span>Links</span></h5>
      <ul><li>Home</li><li>About Evenkeel</li><li>Our Courses</li><li>Special Offers</li><li>Testimonials</li><li>Blog</li><li>FAQs</li><li>Contact Us</li></ul>
    </div>
    <div class="foot-col contact">
      <h5>Contact <span>Details</span></h5>
      <div class="line">Evenkeel Wellness</div>
      <div class="line">120 Meadow Bend, Suite 4<br>Oak Hollow, IL 60500</div>
      <div class="line"><svg viewBox="0 0 14 14"><circle cx="7" cy="7" r="7" fill="#00a990"/></svg>630-555-0184</div>
      <div class="line"><svg viewBox="0 0 14 14"><circle cx="7" cy="7" r="7" fill="#00a990"/></svg>630-555-0172</div>
      <div class="line"><svg viewBox="0 0 14 14"><circle cx="7" cy="7" r="7" fill="#00a990"/></svg>hello@evenkeelwellness.example</div>
    </div>
    <div class="foot-col follow">
      <h5>Follow <span>Us</span></h5>
      <ul><li><i></i>Friendline</li><li><i></i>Chirper</li><li><i></i>Linkpro</li><li><i></i>Circleplus</li></ul>
    </div>
    <div class="foot-mark">Evenkeel Wellness</div>
  </div>
</footer>
<div class="copyright"><div class="wide">© 2024 Evenkeel Wellness. All Rights Reserved.</div></div>

</body>
</html>
```